All Natural Mosquito Repellent

My company, BrightPebble Company has created an all natural mosquito repellent. I already have other all natural products that I have developed and created labels for. I will include a copy of that label so you have something to work from. I will need two labels. One for the front of the bottle and one for the back. The back label will need space for a UPC. The labels need to be 63mm (H) x 39mm (W)

Target Market(s)

Consumers, Organic, People who like natural products

Font styles to use
Other font styles liked:
• A combination of both Serif and Sans Serif

Requirements
Must have
• Use the words Organic, All Natural, Travel size, made in the USA label
Nice to have
• tag line: Don't beat them off. Spray them away.

```html
<!DOCTYPE html>
<html lang="en">
<head>
<meta charset="utf-8">
<title>BrightPebble Mosquito Repellent Labels</title>
<link href="https://fonts.googleapis.com/css2?family=Oswald:wght@500;600&family=Libre+Baskerville&family=Open+Sans:wght@400;600;700&family=Roboto+Slab:wght@800&display=swap" rel="stylesheet">
<style>
  :root {
    --bg: #ffffff;
    --teal: #1aa582;
    --teal-dark: #12997a;
    --teal-soft: #8fd3c1;
    --orange: #f26b1d;
    --ink: #1d1d1d;
    --grey: #4a4a4a;
    --white: #ffffff;
  }
  * { box-sizing: border-box; margin: 0; padding: 0; }
  html, body { width: 1200px; height: 1200px; overflow: hidden; background: var(--bg); }
  .canvas {
    width: 1200px; height: 1200px; display: flex; justify-content: center;
    align-items: center; gap: 90px;
  }
  .label {
    width: 330px; height: 534px; border-radius: 12px; position: relative;
    background: linear-gradient(180deg, #ffffff 0%, #f3f8f7 20%, #ffffff 30%, #cfeee6 52%, var(--teal-soft) 70%, var(--teal) 100%);
    font-family: "Open Sans", sans-serif; color: var(--ink); text-align: center;
    overflow: hidden;
  }
  /* front */
  .brand { position: absolute; top: 40px; left: 0; right: 0; }
  .brand-mark {
    width: 62px; height: 62px; border-radius: 50%; background: #f3b73a;
    margin: 0 auto 8px;
  }
  .brand-name { font-size: 15px; line-height: 18px; font-weight: 400; color: var(--grey); letter-spacing: 0.4px; }
  .brand-sub { font-size: 5.5px; line-height: 8px; color: #555; margin-top: 3px; }
  .line-name { position: absolute; top: 166px; left: 0; right: 0; font-size: 15px; line-height: 20px; }
  .product-title {
    position: absolute; top: 186px; left: 0; right: 0; font-family: "Oswald", sans-serif;
    font-weight: 600; font-size: 31px; line-height: 40px; color: var(--orange); letter-spacing: 0.3px;
  }
  .tagline {
    position: absolute; top: 230px; left: 0; right: 0; font-family: "Libre Baskerville", serif;
    font-size: 17px; line-height: 22px;
  }
  .art {
    position: absolute; top: 286px; left: 90px; width: 150px; height: 128px;
    border-radius: 50%; background: radial-gradient(circle, #ffffff 0%, #d7efe8 70%, transparent 72%);
  }
  .claims {
    position: absolute; top: 428px; left: 58px; right: 66px; height: 26px;
    background: var(--orange); color: var(--white); font-family: "Oswald", sans-serif;
    font-weight: 500; font-size: 11.5px; line-height: 26px; letter-spacing: 0.2px;
  }
  .made {
    position: absolute; bottom: 28px; left: 20px; color: var(--white);
    font-family: "Roboto Slab", serif; font-weight: 800; font-size: 16px; line-height: 1.15;
    display: flex; align-items: center; gap: 4px;
  }
  .made .star { font-size: 8px; }
  .net {
    position: absolute; bottom: 34px; right: 28px; color: var(--white);
    font-family: "Oswald", sans-serif; font-weight: 500; font-size: 12px; line-height: 1.3;
  }
  /* back */
  .back { padding: 28px 24px 0; }
  .section-tag {
    display: inline-block; background: var(--teal-dark); color: var(--white);
    font-size: 10px; line-height: 13px; font-weight: 700; padding: 4px 7px; margin-bottom: 7px;
  }
  .section-body { font-size: 6.6px; line-height: 1.5; margin-bottom: 14px; padding: 0 2px; }
  .address { text-align: left; margin-top: 22px; padding-left: 74px; }
  .address h3 { font-size: 11.5px; font-weight: 600; text-align: center; margin-left: -74px; margin-bottom: 8px; }
  .address p { font-size: 8.8px; line-height: 1.45; }
  .back-foot { position: absolute; left: 18px; right: 20px; bottom: 18px; display: flex; align-items: center; gap: 22px; }
  .upc {
    flex: 1; height: 64px; border: 2px solid var(--ink); display: flex; align-items: center;
    justify-content: center; font-size: 20px; font-weight: 600;
  }
</style>
</head>
<body>
<main class="canvas">
  <section class="label front">
    <div class="brand">
      <div class="brand-mark"></div>
      <div class="brand-name">BrightPebble Company</div>
      <div class="brand-sub">crafted by hand, with love in the U.S.A.</div>
    </div>
    <div class="line-name">PEBBLE</div>
    <h1 class="product-title">MOSQUITO REPELLENT</h1>
    <p class="tagline">“Don't beat them off<br>Spray them away”</p>
    <div class="art" role="img" aria-label="Mosquito inside a red no-entry sign"></div>
    <div class="claims">ORGANIC &#9679; ALL NATURAL &#9679; TRAVEL SIZE</div>
    <div class="made"><span class="star">&#9733;</span><span>Made in<br>the USA</span><span class="star">&#9733;</span></div>
    <div class="net">NET WEIGHT<br>50 ML</div>
  </section>

  <section class="label back">
    <div class="section-tag">DIRECTION FOR USE:</div>
    <p class="section-body">There are many variations of passages of Lorem Ipsum available, but the majority have suffered alteration in some form, by injected humour, or randomised words which don't look even slightly believable. If you are going to use a passage of Lorem Ipsum, you need to be sure there isn't anything embarrassing hidden in the middle of text.</p>
    <div class="section-tag">PRECAUTION:</div>
    <p class="section-body">There are many variations of passages of Lorem Ipsum available, but the majority have suffered alteration in some form, by injected humour, or randomised words which don't look even slightly believable.</p>
    <div class="section-tag">INGREDIENTS:</div>
    <p class="section-body">There are many variations of passages of Lorem Ipsum available, but the majority have suffered alteration in some form, by injected humour, or randomised words which don't look even slightly believable.</p>
    <div class="section-tag">STORAGE:</div>
    <p class="section-body">Store in a cool and dry place. Place empty container in trsh or recycle.</p>
    <div class="address">
      <h3>Company Address:</h3>
      <p>Lorem Ipsum is simply dummy<br>text of the printing and typesetting<br>industry.</p>
    </div>
    <div class="back-foot">
      <svg width="38" height="36" viewBox="0 0 38 36" aria-label="Recycle">
        <g fill="none" stroke="#1d1d1d" stroke-width="4" stroke-linejoin="round">
          <path d="M13 12 L19 3 L25 12"/>
          <path d="M30 17 L34 27 L24 29"/>
          <path d="M14 31 L4 27 L9 18"/>
        </g>
      </svg>
      <div class="upc">UPC</div>
    </div>
  </section>
</main>
</body>
</html>
```